Business Cards for a law firm

Business cards for our law firm. Use our silhoette logo and OAK PARTNERS - check our website (www.oakpartners.example)

Contact Information for Business Card

our silhouette logo, OAK PARTNERS, 800-555-0147, Dorian Pemberton, dorian@oakpartners.example

Requirements
Must have
• our silhouette logo, OAK PARTNERS, 800-555-0147, Dorian Pemberton, dorian@oakpartners.example

```html
<!DOCTYPE html>
<html lang="en">
<head>
<meta charset="utf-8">
<title>Oak Partners – Business Card</title>
<link rel="stylesheet" href="https://fonts.googleapis.com/css2?family=Roboto:wght@300;400;700&display=swap">
<style>
  :root {
    --page-bg: #e3e8ea;
    --navy: #223369;
    --navy-deep: #1f2f63;
    --sky: #3a9ad8;
    --ink: #263a7a;
    --white: #ffffff;
  }
  * { box-sizing: border-box; margin: 0; padding: 0; }
  html, body {
    width: 1200px;
    height: 960px;
    overflow: hidden;
    background: var(--page-bg);
    font-family: "Roboto", Arial, sans-serif;
  }
  .card {
    position: absolute;
    left: 248px;
    width: 704px;
    height: 402px;
  }
  .card-front {
    top: 58px;
    background: var(--navy);
    overflow: hidden;
  }
  .front-pattern {
    position: absolute;
    inset: 0;
    background:
      radial-gradient(ellipse at 100% 0%, rgba(58,154,216,0.85) 0%, rgba(58,154,216,0.35) 35%, rgba(58,154,216,0) 62%),
      linear-gradient(180deg, var(--navy) 0%, var(--navy-deep) 100%);
  }
  .front-wordmark {
    position: absolute;
    left: 258px;
    top: 158px;
    color: var(--white);
    font-weight: 300;
    font-size: 40px;
    line-height: 40px;
    letter-spacing: 1px;
  }
  .card-back {
    top: 500px;
    background: var(--white);
  }
  .back-wordmark {
    position: absolute;
    left: 28px;
    top: 188px;
    color: var(--ink);
    font-weight: 400;
    font-size: 24px;
    letter-spacing: 0.5px;
  }
  .divider {
    position: absolute;
    left: 351px;
    top: 80px;
    width: 1px;
    height: 241px;
    background: var(--ink);
  }
  .contact {
    position: absolute;
    left: 399px;
    top: 132px;
    color: var(--ink);
  }
  .person-name {
    font-size: 26px;
    letter-spacing: 0.5px;
    white-space: nowrap;
  }
  .person-name .first { font-weight: 700; }
  .person-name .last { font-weight: 300; }
  .contact-list {
    list-style: none;
    margin-top: 26px;
  }
  .contact-list li {
    display: flex;
    align-items: center;
    height: 22.5px;
    font-size: 18px;
    letter-spacing: 0.4px;
  }
  .contact-list svg {
    width: 16px;
    height: 16px;
    margin-right: 11px;
    flex: none;
  }
</style>
</head>
<body>
  <section class="card card-front">
    <div class="front-pattern" role="img" aria-label="Repeating pattern of the firm's mark fading from light blue to navy"></div>
    <div class="front-wordmark">OAK<br>PARTNERS</div>
  </section>

  <section class="card card-back">
    <div class="back-wordmark">OAK PARTNERS</div>
    <div class="divider"></div>
    <div class="contact">
      <h1 class="person-name"><span class="first">DORIAN</span> <span class="last">PEMBERTON</span></h1>
      <ul class="contact-list">
        <li>
          <svg viewBox="0 0 16 16" aria-hidden="true"><path fill="var(--ink)" d="M3.5 1.5l2.3 2.6-1.3 1.6c.8 1.8 2.1 3.2 3.9 4.1l1.6-1.3 2.6 2.3-1.3 2.1C6.8 12.4 2.9 8.6 2.4 3z"/></svg>
          800-555-0147
        </li>
        <li>
          <svg viewBox="0 0 16 16" aria-hidden="true"><circle cx="8" cy="8" r="6.5" fill="none" stroke="var(--ink)" stroke-width="1.5"/><path d="M1.5 8h13M8 1.5c-2.5 3-2.5 10 0 13M8 1.5c2.5 3 2.5 10 0 13" fill="none" stroke="var(--ink)" stroke-width="1.2"/></svg>
          www.oakpartners.example
        </li>
        <li>
          <svg viewBox="0 0 16 16" aria-hidden="true"><rect x="1.5" y="4" width="13" height="9.5" fill="none" stroke="var(--ink)" stroke-width="1.5"/><path d="M1.5 4l6.5 5 6.5-5" fill="none" stroke="var(--ink)" stroke-width="1.5"/></svg>
          dorian@oakpartners.example
        </li>
      </ul>
    </div>
  </section>
</body>
</html>
```